Core Value Graphic for a Service Disabled and Minority Certified contractor

My company, Keystone Aid Partners, is a US Federal Contractor that hires veterans and service disabled veterans. Our website is www.keystoneaid7.example. We work hard to maintain a 50:50 split between veterans and non-veterans on our team. Our tagline is "To Find a Better Way." We are continually looking to integrate technology and efficiency into all that we do.

I want a way to express our company core values visually so that our employees and customers alike can read them and get a sense of who we are, what drives us to succeed, and what makes up our team DNA.

I need an artist like you to help me represent our core values visually. In a manner that I can print it out on an 8"X11" sheet of paper or a large 48" X 48" poster, without losing the visual clarity or that it pixelates out of focus. I am looking for a color scheme that is patriotic with Red, White, and Blues and similar hues. I would also like to incorporate my logo and tagline into the design in some manner.

I have attached several examples of a Core Value Grids from other companies. I am hopeful it will inspire you, and a get your brain juices flowing to provide me with a knockout Core Value Grid that will rock only you can provide! I also include a copy of my company Core Values and a copy of our Logo.

Looking forward to seeing your creations. Thanks.

Target Market(s)

Employees, any potential strategic alliance partners, and customers.

Industry/Entity Type

Contractor

Requirements
Must have
• Patriotic feel and have my logo someplace on the document.

```html
<!DOCTYPE html>
<html lang="en">
<head>
<meta charset="utf-8">
<title>Keystone Aid Partners – Our Core Values</title>
<link rel="stylesheet" href="https://fonts.googleapis.com/css2?family=Montserrat:wght@800&family=Oswald:wght@600&family=PT+Sans:wght@700&family=PT+Sans+Narrow:wght@400;700&display=swap">
<style>
  :root {
    --navy: #1b3566;
    --navy-deep: #12264d;
    --blue: #1e4d80;
    --teal: #1c5a78;
    --teal-deep: #134a63;
    --red: #c21b24;
    --red-deep: #8a0d14;
    --gray: #76787b;
    --gray-deep: #55575a;
    --stripe: #d9dadc;
    --white: #ffffff;
  }
  html, body { margin: 0; padding: 0; overflow: hidden; background: var(--white); }
  .poster {
    position: relative;
    width: 927px;
    height: 1200px;
    overflow: hidden;
    background:
      repeating-linear-gradient(to bottom, transparent 0 8px, var(--stripe) 8px 13px),
      var(--white);
  }
  .layer { position: absolute; inset: 0; width: 927px; height: 1200px; }
  .title-text {
    font-family: "Montserrat", sans-serif;
    font-weight: 800;
    fill: var(--navy);
  }
  .banner-text {
    font-family: "PT Sans", sans-serif;
    font-weight: 700;
    fill: var(--white);
  }

  .ribbon {
    position: absolute;
    width: 124px;
    box-sizing: border-box;
    padding: 12px 10px;
    transform: rotate(-10deg);
    transform-origin: left top;
    color: var(--white);
    text-align: center;
    box-shadow: 3px 4px 8px rgba(0,0,0,0.25);
  }
  .ribbon h3 {
    margin: 4px 0 3px;
    font-family: "Oswald", sans-serif;
    font-weight: 600;
    font-size: 17px;
    line-height: 0.95;
    text-transform: uppercase;
  }
  .ribbon p {
    margin: 0 0 7px;
    font-family: "PT Sans Narrow", sans-serif;
    font-size: 11px;
    line-height: 1.12;
  }
  .ribbon--safety  { left: 8px;   top: 297px; height: 600px; background: linear-gradient(90deg, var(--red-deep), var(--red)); }
  .ribbon--wingman { left: 159px; top: 363px; height: 580px; background: linear-gradient(90deg, var(--red-deep), var(--red)); }
  .ribbon--learn   { left: 303px; top: 428px; height: 560px; background: linear-gradient(90deg, var(--gray-deep), var(--gray)); }
  .ribbon--boldly  { left: 454px; top: 475px; height: 620px; background: linear-gradient(90deg, var(--teal-deep), var(--teal)); }
  .ribbon--troops  { left: 614px; top: 560px; height: 520px; background: linear-gradient(90deg, var(--navy-deep), var(--navy)); }

  .brand {
    position: absolute;
    left: 26px;
    top: 950px;
    display: flex;
    align-items: center;
    gap: 12px;
    z-index: 4;
  }
  .brand-mark { width: 30px; height: 30px; background: var(--red); }
  .brand-name {
    font-family: "PT Sans", sans-serif;
    font-weight: 700;
    font-size: 30px;
    line-height: 1;
    color: var(--navy);
  }
  .footer-band { z-index: 3; }
  .tagline {
    font-family: "PT Sans", sans-serif;
    font-weight: 700;
    fill: var(--white);
  }
</style>
</head>
<body>
<main class="poster">

  <svg class="layer stripes-accent" viewBox="0 0 927 1200" aria-hidden="true">
    <g fill="#1e4d80" opacity="0.45">
      <rect x="700" y="619" width="227" height="5"/>
      <rect x="700" y="645" width="227" height="5"/>
      <rect x="700" y="671" width="227" height="5"/>
      <rect x="700" y="697" width="227" height="5"/>
      <rect x="700" y="723" width="227" height="5"/>
      <rect x="700" y="749" width="227" height="5"/>
      <rect x="700" y="775" width="227" height="5"/>
      <rect x="700" y="801" width="227" height="5"/>
      <rect x="700" y="827" width="227" height="5"/>
    </g>
  </svg>

  <svg class="layer banners" viewBox="0 0 927 1200" role="img" aria-label="Our core values">
    <defs>
      <linearGradient id="grad-red" x1="0" x2="1"><stop offset="0" stop-color="#8a0d14"/><stop offset="1" stop-color="#c21b24"/></linearGradient>
      <linearGradient id="grad-gray" x1="0" x2="1"><stop offset="0" stop-color="#55575a"/><stop offset="1" stop-color="#76787b"/></linearGradient>
      <linearGradient id="grad-blue" x1="0" x2="1"><stop offset="0" stop-color="#134a63"/><stop offset="1" stop-color="#1e4d80"/></linearGradient>
      <linearGradient id="grad-navy" x1="0" x2="1"><stop offset="0" stop-color="#12264d"/><stop offset="1" stop-color="#1b3566"/></linearGradient>
    </defs>

    <g transform="rotate(-10 40 150)">
      <text class="title-text" x="40" y="150" font-size="52">OUR</text>
    </g>
    <g transform="rotate(-10 45 215)">
      <text class="title-text" x="45" y="215" font-size="80" textLength="540" lengthAdjust="spacingAndGlyphs">CORE VALUES</text>
    </g>

    <g transform="rotate(-10 420 195)">
      <rect x="-100" y="166" width="1200" height="58" fill="url(#grad-red)"/>
      <text class="banner-text" x="420" y="206" font-size="32" text-anchor="middle">Everyone comes back to the Green Zone.</text>
    </g>
    <g transform="rotate(-10 440 286)">
      <rect x="145" y="259" width="960" height="54" fill="url(#grad-red)"/>
      <text class="banner-text" x="440" y="297" font-size="30" text-anchor="middle">Never leave your wingman.</text>
    </g>
    <g transform="rotate(-10 556 356)">
      <rect x="290" y="329" width="800" height="54" fill="url(#grad-gray)"/>
      <text class="banner-text" x="556" y="367" font-size="30" text-anchor="middle">Fail quickly and learn.</text>
    </g>
    <g transform="rotate(-10 697 405)">
      <rect x="440" y="378" width="640" height="54" fill="url(#grad-blue)"/>
      <text class="banner-text" x="697" y="416" font-size="30" text-anchor="middle">Boldly go. Seek. Find.</text>
    </g>
    <g transform="rotate(-10 800 500)">
      <rect x="600" y="473" width="450" height="54" fill="url(#grad-navy)"/>
    </g>
  </svg>

  <section class="ribbon ribbon--safety">
    <h3>What it means</h3>
    <p>Safety takes precedence over every phase of the day's operation.</p>
    <h3>How to express it</h3>
    <p>Anyone can call a stop to the work in progress if an unsafe act is occurring. In fact, it is each team member's duty to do so, rectify the unsafe issue, then proceed. Never hesitate; everyone comes back. Finally, each After Action Review begins with discussing safety issues. We always let everyone on the team know of an unsafe situation, so it can be avoided in the future.</p>
    <h3>Result</h3>
    <p>All team members go home to their loved ones each day to pursue their individual happiness.</p>
  </section>

  <section class="ribbon ribbon--wingman">
    <h3>What it means</h3>
    <p>We always help your team members to be successful. Commitment to each other and to our own personal integrity is the fuel that empowers us.</p>
    <h3>How to express it</h3>
    <p>If a Wingman is having challenges accomplishing their individual priorities or completing their assigned mission, volunteer to help them to do so. The same goes for Subs/Suppliers as well. We help those who help us succeed. Never hesitate; everyone comes back. Always look to establish the best win-win relationship possible, and do what you can to support them if they get into a bind.</p>
    <h3>Result</h3>
    <p>Be there for them and they will be there for us.</p>
  </section>

  <section class="ribbon ribbon--learn">
    <h3>What it means</h3>
    <p>If you're not making mistakes, you're not taking enough chances or getting out of your comfort zone.</p>
    <h3>How to express it</h3>
    <p>Use your best judgement when trying something new. But, don't let your pride keep you from saying, "I was wrong" when your idea doesn't work. We trust you will know when it's time to dump the idea, or stop doing something that doesn't work.</p>
    <h3>Result</h3>
    <p>No one will ever be penalized for making a mistake. Don't be afraid to try something you believe will work. That's how we grow ourselves and our team members.</p>
  </section>

  <section class="ribbon ribbon--boldly">
    <h3>What it means</h3>
    <p>We are innovators; it is the fabric that makes up our company.</p>
    <h3>How to express it</h3>
    <p>We're early adopters of technology. We quickly evaluate new technologies or processes that could separate us from our competition. Then we implement and evaluate these new technologies. We dump it quickly if we see it is not helping us achieve "Commander's Intent." We haul the guns to the fight. We inquire continuously and attack, attack, attack.</p>
    <h3>Result</h3>
    <p>We will be ahead of our competition. It's the mechanism that helps us scale. Prosperity favors the bold!</p>
  </section>

  <section class="ribbon ribbon--troops">
    <h3>What it means</h3>
    <p>No leader will put themselves ahead of their subordinates.</p>
    <h3>How to express it</h3>
    <p>We lead by example. Demonstrate the moral courage and discipline to do the right thing at the highest level of quality.</p>
    <h3>Result</h3>
    <p>Every new team member will quickly realize their leaders genuinely care for their welfare and success. This is the best way to drive Esprit de Corps and achieve excellence.</p>
  </section>

  <div class="brand">
    <span class="brand-mark"></span>
    <span class="brand-name">Keystone Aid Partners</span>
  </div>

  <svg class="layer footer-band" viewBox="0 0 927 1200" aria-hidden="true">
    <defs>
      <linearGradient id="grad-footer" x1="0" x2="1"><stop offset="0" stop-color="#12264d"/><stop offset="1" stop-color="#1b3566"/></linearGradient>
    </defs>
    <polygon points="0,1070 927,907 927,1200 0,1200" fill="url(#grad-footer)"/>
    <polygon points="0,1070 927,907 927,913 0,1076" fill="#ffffff" opacity="0.5"/>
    <g transform="rotate(-10 70 1150)">
      <text class="tagline" x="70" y="1150" font-size="50">“TO FIND A BETTER WAY”</text>
    </g>
    <g transform="rotate(-10 545 1128)">
      <text class="tagline" x="545" y="1128" font-size="30" text-anchor="middle">Troops (Team Members) eat first.</text>
    </g>
  </svg>

</main>
</body>
</html>
```